Brightfen Business Card Redesign & Logo Update

We need to update our business cards to something more modern and fresh. Brightfen can provide the current color schemes and old design examples, but welcome creativity in helping us with this redesign. PLEASE NOTE that we no longer utilize the "tree" and/or "leaf" imagery in our branding. If able would apprecaite an update on the quality of our "words only" logo in Ai. / PNG formats too.

Target Market(s)

Investors, landowners, corporate partners, contractors

Industry/Entity Type

Environmental Restoration & Conservation

Contact Information for Business Card

Logo, persons name, title, mailing address, phone and email, website url

Font styles to use
Other font styles liked:
• Merriweather

Requirements
Nice to have
• Logo, persons name, title, mailing address, phone and email, website url, but open to ideams
Should not have
• No all back backgrounds

```html
<!DOCTYPE html>
<html lang="en">
<head>
<meta charset="utf-8">
<title>Brightfen Business Cards</title>
<link href="https://fonts.googleapis.com/css2?family=Merriweather:wght@400;700;900&display=swap" rel="stylesheet">
<style>
  :root {
    --green: #177c3e;
    --orange: #ea7b22;
    --ink: #1d1d1d;
    --paper: #ffffff;
    --backdrop: #e7e8ea;
  }
  * { box-sizing: border-box; margin: 0; padding: 0; }
  html, body {
    width: 1200px; height: 864px; overflow: hidden;
    background: var(--backdrop);
    font-family: "Merriweather", Georgia, serif;
  }
  .sheet {
    width: 1200px; height: 864px;
    display: flex; flex-direction: column;
    align-items: center; justify-content: center; gap: 44px;
  }
  .card {
    position: relative;
    width: 640px; height: 366px;
    background: var(--paper);
    box-shadow: 0 6px 18px rgba(0,0,0,.12);
    overflow: hidden;
  }
  /* Front */
  .card--front { display: flex; align-items: center; justify-content: center; }
  .wordmark {
    display: flex; align-items: center; gap: 14px;
  }
  .wordmark__dot {
    width: 22px; height: 22px; border-radius: 50%;
    background: var(--green);
  }
  .wordmark__name {
    font-weight: 900; color: var(--green);
    font-size: 58px; letter-spacing: 1px; line-height: 1;
    text-transform: uppercase;
  }
  /* Back */
  .card--back .wordmark {
    position: absolute; top: 70px; left: 190px;
  }
  .card--back .wordmark__name { font-size: 44px; }
  .card--back .wordmark__dot { width: 18px; height: 18px; }
  .person {
    position: absolute; left: 120px; top: 168px;
    text-align: right; width: 220px;
  }
  .person__name {
    font-weight: 900; font-size: 22px; letter-spacing: .5px;
    text-transform: uppercase; line-height: 1.2;
  }
  .person__first { color: var(--orange); }
  .person__last { color: var(--green); }
  .person__title {
    font-size: 16px; color: var(--ink); margin-top: 4px;
  }
  .divider {
    position: absolute; left: 358px; top: 150px;
    width: 1.5px; height: 102px; background: var(--green);
  }
  .contact {
    position: absolute; left: 376px; top: 150px;
    list-style: none;
    font-size: 14.5px; color: var(--ink); line-height: 1;
  }
  .contact__item {
    display: flex; align-items: center; gap: 8px;
    height: 28px;
  }
  .contact__icon { width: 14px; height: 14px; flex: none; fill: var(--green); }
  .band {
    position: absolute; left: 0; right: 0; top: 286px; height: 52px;
    background: var(--green);
    display: flex; align-items: center; justify-content: center;
    color: var(--paper); font-size: 15.5px; letter-spacing: .3px;
  }
</style>
</head>
<body>
<main class="sheet">

  <section class="card card--front" aria-label="Business card front">
    <div class="wordmark">
      <span class="wordmark__dot"></span>
      <span class="wordmark__name">Brightfen</span>
    </div>
  </section>

  <section class="card card--back" aria-label="Business card back">
    <div class="wordmark">
      <span class="wordmark__dot"></span>
      <span class="wordmark__name">Brightfen</span>
    </div>

    <div class="person">
      <p class="person__name"><span class="person__first">Nolan</span> <span class="person__last">Reyes</span></p>
      <p class="person__title">Founder</p>
    </div>

    <div class="divider"></div>

    <ul class="contact">
      <li class="contact__item">
        <svg class="contact__icon" viewBox="0 0 24 24" aria-hidden="true"><path d="M6.6 10.8a15.1 15.1 0 0 0 6.6 6.6l2.2-2.2c.3-.3.7-.4 1-.2 1.1.4 2.3.6 3.6.6.6 0 1 .4 1 1V20c0 .6-.4 1-1 1A17 17 0 0 1 3 4c0-.6.4-1 1-1h3.5c.6 0 1 .4 1 1 0 1.3.2 2.5.6 3.6.1.3 0 .7-.2 1z"/></svg>
        (555) 214-0187
      </li>
      <li class="contact__item">
        <svg class="contact__icon" viewBox="0 0 24 24" aria-hidden="true"><path d="M2 5h20v14H2z M4 7v.4l8 5.3 8-5.3V7z" fill-rule="evenodd"/></svg>
        hello@brightfen.com
      </li>
      <li class="contact__item">
        <svg class="contact__icon" viewBox="0 0 24 24" aria-hidden="true"><circle cx="12" cy="12" r="10"/><path d="M2 12h20M12 2c3 3 3 17 0 20M12 2c-3 3-3 17 0 20" stroke="#fff" stroke-width="1.5" fill="none"/></svg>
        www.brightfen.com
      </li>
    </ul>

    <div class="band">14 Marsh Lane, Suite 220, PO Box 7812, Fenton</div>
  </section>

</main>
</body>
</html>
```